Road Construction Company needs business cards

We would like a new business card designed for our business.

We're a road construction company based in Qld, Australia.

Can the business card please have the following information on it.

Name: Warren Halbeck
Position: General Manager
Phone: 0472 915 348
Email: Warren.halbeck@tovrin.com.au
Address: 87 Marrow Ave, Pendlebay, QLD, 4023
Website: www.tovrin.com.au

Visually we'd like the card to be professional and simple.

Attached is our logo.

Our website is www.tovrin.com.au

Target Market(s)

Men aged 25-60

Contact Information for Business Card

As listed in project description

Font styles to use
Serif

Requirements
Must have
• Large logo on back of card

```html
<!DOCTYPE html>
<html lang="en">
<head>
<meta charset="utf-8">
<title>Tovrin Road Construction – Business Card</title>
<link href="https://fonts.googleapis.com/css2?family=Arimo:wght@400;700&display=swap" rel="stylesheet">
<style>
  :root {
    --backdrop: #ececec;
    --card: #2f2f30;
    --card-deep: #1c1c1d;
    --band: #3a3a3c;
    --blue: #2a8fd8;
    --logo-blue: #1f6fc4;
    --ink: #f2f2f2;
    --rule: #9a9a9a;
  }
  * { box-sizing: border-box; margin: 0; padding: 0; }
  html, body {
    width: 1200px; height: 802px; overflow: hidden;
    background: var(--backdrop);
    font-family: "Arimo", Arial, sans-serif;
  }
  .stage {
    position: relative; width: 1200px; height: 802px;
    display: flex; align-items: center; justify-content: center; gap: 44px;
  }
  .card {
    position: relative; width: 520px; height: 297px;
    background: var(--card); overflow: hidden;
    box-shadow: 0 6px 18px rgba(0,0,0,.22);
  }
  /* Front */
  .front .brand {
    position: absolute; left: 38px; top: 50%; transform: translateY(-50%);
    font-weight: 700; font-size: 40px; letter-spacing: 1px; color: var(--logo-blue);
  }
  .front .divider {
    position: absolute; left: 236px; top: 58px; width: 1px; height: 182px;
    background: var(--rule);
  }
  .front .details {
    position: absolute; left: 256px; top: 58px; color: var(--ink);
    font-size: 13px; line-height: 1.45;
  }
  .details .name {
    font-weight: 700; font-size: 18px; color: var(--blue);
    text-transform: uppercase; line-height: 1.1;
  }
  .details .role { margin-bottom: 10px; }
  .details .address { margin-bottom: 10px; }
  .contact { list-style: none; }
  .contact li { display: flex; align-items: center; gap: 7px; }
  .contact svg { width: 11px; height: 11px; flex: none; }
  /* Back */
  .back .band {
    position: absolute; inset: 0;
  }
  .back .brand {
    position: absolute; right: 40px; bottom: 62px;
    font-weight: 700; font-size: 44px; letter-spacing: 1px; color: var(--ink);
  }
</style>
</head>
<body>
<main class="stage">
  <section class="card front" aria-label="Card front">
    <div class="brand">TOVRIN</div>
    <div class="divider"></div>
    <div class="details">
      <p class="name">Warren Halbeck</p>
      <p class="role">General Manager</p>
      <p class="address">87 Marrow Ave<br>Pendlebay, QLD, 4023</p>
      <ul class="contact">
        <li>
          <svg viewBox="0 0 12 12" aria-hidden="true"><path d="M2.5 1.5l2 2-1 1.2c.6 1.4 1.6 2.4 3 3L7.7 6.7l2 2-1.3 1.8C5 10.3 1.7 7 1.5 3.3z" fill="var(--blue)"/></svg>
          0472 915 348
        </li>
        <li>
          <svg viewBox="0 0 12 12" aria-hidden="true"><rect x="1" y="2.5" width="10" height="7" fill="none" stroke="var(--blue)" stroke-width="1.1"/><path d="M1 2.8l5 3.7 5-3.7" fill="none" stroke="var(--blue)" stroke-width="1.1"/></svg>
          Warren.halbeck@tovrin.com.au
        </li>
        <li>
          <svg viewBox="0 0 12 12" aria-hidden="true"><circle cx="6" cy="6" r="5" fill="var(--blue)"/><path d="M1 6h10M6 1c-2 2.6-2 7.4 0 10M6 1c2 2.6 2 7.4 0 10" fill="none" stroke="var(--card)" stroke-width=".8"/></svg>
          www.tovrin.com.au
        </li>
      </ul>
    </div>
  </section>

  <section class="card back" aria-label="Card back">
    <svg class="band" viewBox="0 0 520 297" preserveAspectRatio="none" aria-hidden="true">
      <defs>
        <linearGradient id="bandShade" x1="0" y1="0" x2="1" y2="1">
          <stop offset="0" stop-color="#242425"/>
          <stop offset="1" stop-color="#3d3d3f"/>
        </linearGradient>
      </defs>
      <polygon points="0,0 120,0 250,297 0,297" fill="var(--card-deep)"/>
      <polygon points="120,0 175,0 305,297 250,297" fill="url(#bandShade)"/>
    </svg>
    <div class="brand">TOVRIN</div>
  </section>
</main>
</body>
</html>
```